Dentistry Office

We want a new design for a Dentist's office website.

The theme is: "We provide high quality, state-of-the-art, dental care in a comfortable, caring environment."

The site currently has a menu on the left of the page with about 40 items on it. There is a great deal of textual content on each page, plus several illustrations.

We want to do this using CSS, so we need specifications in the CSS for all possible elements. The CSS needs to be named in a logical manner for easy use.

Every dentist on the planet seems to use lots of Flash. We don't want to because it is so distracting. We are looking for an elegant solution targeting 24-55 age group, but not excluding anyone.

The following (from another dentist's site) can give you a taste of what we want to communicate on the site:

"After 20 years of teaching dentists how to refine their technique and many years of writing textbooks, I currently devote my time to my office and the hands-on practice of dentistry. I'd like to welcome you personally to my dental practice, and I invite you to meet my highly experienced team of professionals.

"We have offered complete dental care of the highest quality since 1978. We provide Preventive Services, Tooth Whitening and Cosmetic Dentistry for a beautiful smile, Endodontics (root canal treatment) to treat painful teeth, Sedation Dentistry so you can relax, and Dental Implants to restore what is missing. We offer total care.

"Our approach to your health is simple: We use our education, experience and dedication to provide every patient with superior dental care.

"This passion for excellence is not just a goal, but a standard every member of our team holds.

"We also pride ourselves with our state of the art procedures, training and technology. This includes creating a beautiful smile using techniques that preserve as much of the original tooth as possible.

"Our abilities are renowned throughout the dental profession and I hope if you have any questions you will contact us by an e-mail note, by phone or just by dropping by."

Keep in mind the screen shape and dimensions. Your design needs to work in the normal screen proportions, regardless of how it looks when you post it here. Scrolling is OK, but the first impression needs to work.
Updates

Keep in mind that there will be about 250 words, or more, on each page.

Competitors web sites:

http://www.brindlecovedentist.example/

http://www.brindlecovedentalcare.example/

http://www.grinsbymarlowvaledental.example/

http://www.tenbyfamilydentalcare.example/

http://www.quelmardental.example/

http://www.dovrinadental.example/

We need to compete with these.

Target Market(s)

Generally adults seeking the most experienced and comfortable-to-be-with dentist.

Industry/Entity Type

Training

Requirements
Must have
• Must stand apart from other dentists.
• Must be elegant.
• Must have a horizontal menu structure across all columns, NOT a vertical that requires scrolling, no popout, pop down, etc. menus.
• We are looking for something special.
• Do not waste your time or ours putting up templates and things you have used before.
• Personally, I do not see how someone outside the US can understand the northern California dental market. But you are welcome to try.
Should not have
• Flash or graphics that move
• The look of a template
• Folksy fonts
• Looks like you used it 20 times before

```html
<!DOCTYPE html>
<html lang="en">
<head>
<meta charset="utf-8">
<title>Brindle Cove Dentist – Mara Haldane, DDS</title>
<link rel="stylesheet" href="https://fonts.googleapis.com/css2?family=Open+Sans:ital,wght@0,400;0,700;1,400&display=swap">
<style>
:root{
  --page:#161417;
  --panel:#1f1c21;
  --nav:#0d0c0e;
  --ink:#e9e6ea;
  --muted:#b9b3bd;
  --magenta:#c8237a;
  --plum:#7a2a7c;
  --violet:#8c3fb0;
  --education:#2f5fae;
  --preventive:#3f8f2f;
  --cosmetic:#7b3a9a;
  --restore:#b0214a;
  --visit:#a640b8;
}
*{margin:0;padding:0;box-sizing:border-box}
html,body{width:814px;height:1200px;overflow:hidden}
body{background:var(--page);color:var(--ink);font-family:"Open Sans",Arial,sans-serif;font-size:11px;line-height:1.45;position:relative}
a{color:inherit;text-decoration:none}

.top-nav{position:absolute;left:0;top:0;width:814px;height:22px;background:var(--nav);display:flex;justify-content:flex-end;align-items:center;padding-right:14px;gap:0}
.top-nav a{font-size:10px;color:var(--ink);padding:0 12px;border-left:1px solid #3a3640}
.top-nav a:first-child{border-left:none}

.site-title{position:absolute;left:14px;top:26px;width:560px;color:var(--magenta);font-size:12px;line-height:1.3;font-weight:700}
.site-title .address{display:block;font-weight:400;color:var(--muted);font-size:10px}

.hero{position:absolute;left:0;top:68px;width:814px;height:420px}
.hero-glow{position:absolute;left:0;top:0;width:540px;height:420px;background:radial-gradient(circle at 40% 40%,#4a1f50 0%,#2a1730 45%,var(--page) 80%)}
.intro-card{position:absolute;left:27px;top:24px;width:218px;height:210px;background:linear-gradient(160deg,#9a3aa0,#5b1f68);padding:14px 16px;font-style:italic;font-size:13px;line-height:1.5;color:#fff}
.award-card{position:absolute;left:297px;top:27px;width:243px;height:112px;background:linear-gradient(160deg,#b32a86,#6e1f63);padding:12px 14px;font-size:12px;line-height:1.45;color:#fff}
.hero-photo{position:absolute;left:540px;top:0;width:274px;height:422px;background:linear-gradient(170deg,#d9d4d8 0%,#b9a9b3 55%,#6d5366 100%)}

.service-tabs{position:absolute;left:14px;top:492px;width:786px;display:grid;grid-template-columns:repeat(5,1fr);gap:4px}
.tab-title{display:block;height:24px;line-height:24px;text-align:center;font-weight:700;font-style:italic;font-size:13px;color:#fff}
.tab-education .tab-title{background:var(--education)}
.tab-preventive .tab-title{background:var(--preventive)}
.tab-cosmetic .tab-title{background:var(--cosmetic)}
.tab-restore .tab-title{background:var(--restore)}
.tab-visit .tab-title{background:var(--visit)}
.tab-links{list-style:none;padding:6px 8px;font-size:9.5px;line-height:1.4}
.tab-links li{color:var(--ink)}

.provides{position:absolute;left:27px;top:690px;width:210px}
.section-heading{color:var(--magenta);font-size:14px;font-weight:700;margin-bottom:8px}
.provides p{font-size:10px;margin-bottom:7px;color:var(--ink)}
.side-links{margin-top:16px}
.side-links a{display:block;color:var(--magenta);font-size:11px;margin-bottom:4px}

.commitment{position:absolute;left:262px;top:680px;width:538px;background:var(--panel);padding:10px 16px 14px}
.commitment p{font-size:10.5px;margin-bottom:7px;color:var(--ink)}
.commitment .signoff{margin-top:8px}
.commitment .offer{color:var(--magenta);margin-top:12px;margin-bottom:2px}
.commitment .fine{font-size:9px;color:var(--muted);margin-bottom:2px}
</style>
</head>
<body>

<nav class="top-nav">
  <a href="#">Home</a>
  <a href="#">Patient Information</a>
  <a href="#">Services we offer</a>
  <a href="#">Meet Dr. Haldane</a>
  <a href="#">Our Staff</a>
  <a href="#">Contact us/Links</a>
</nav>

<header class="site-title">
  Brindle Cove Dentist – Mara Haldane, DDS, Providing Cosmetic Dentistry Excellence to Patients in Brindle Cove, Marlow Vale County and the North Coast Bay Area
  <span class="address">Located at 48 Orchard Lane, Ste B-2, Brindle Cove, CA 90000</span>
</header>

<section class="hero">
  <div class="hero-glow"></div>
  <div class="intro-card">In Brindle Cove, when you're a patient of Dr. Haldane, you can be confident that you're receiving care from the most experienced, knowledgeable, and skilled cosmetic dentist in Marlow Vale County.</div>
  <div class="award-card">Dr. Haldane is an award-winning leader in restorative dentistry and dental professionalism. His true dedication, and talent ensure you a pleasant experience and superb, long-lasting results.</div>
  <div class="hero-photo" role="img" aria-label="Photograph of a smiling woman patient"></div>
</section>

<section class="service-tabs">
  <div class="tab-education">
    <a class="tab-title" href="#">Education</a>
    <ul class="tab-links">
      <li>Emergency Dental Care</li><li>Your Mouth</li><li>Your Teeth</li><li>Cracked Tooth?</li><li>Missing a Tooth?</li><li>Sensitive Teeth</li><li>Dry Mouth</li><li>Tooth Grinding</li><li>Sleep Dentistry</li><li>Video</li>
    </ul>
  </div>
  <div class="tab-preventive">
    <a class="tab-title" href="#">Preventative</a>
    <ul class="tab-links">
      <li>What is Preventive Care?</li><li>Taking Care of Your Teeth</li><li>Eating Right</li><li>Dental Check-Ups</li><li>Sealants</li><li>Periodontal Disease</li><li>Kicking the Habit</li><li>Night Guards</li><li>Dental X-Rays</li><li>Antibiotics with Treatment</li>
    </ul>
  </div>
  <div class="tab-cosmetic">
    <a class="tab-title" href="#">Cosmetics</a>
    <ul class="tab-links">
      <li>Cosmetic Dentistry</li><li>Bleaching and Whitening</li><li>Cosmetic Bonding</li><li>Esthetic Veneers</li><li>Tooth Shaping</li>
    </ul>
  </div>
  <div class="tab-restore">
    <a class="tab-title" href="#">Restorations</a>
    <ul class="tab-links">
      <li>Crowns/Caps: Each Step</li><li>Tooth Fillings</li><li>Porcelain Bridges</li><li>Dental Implants</li><li>Bridge Replacement</li><li>Treatment Dentures</li><li>Root Canals</li><li>Tooth Extractions</li><li>Treating Cracked Teeth</li><li>Periodontal (gum) Treatment</li>
    </ul>
  </div>
  <div class="tab-visit">
    <a class="tab-title" href="#">Visiting our office</a>
    <ul class="tab-links">
      <li>Your First Visit</li><li>Office Staff</li><li>Map</li><li>Financial Policy</li><li>Dental Insurance</li>
    </ul>
  </div>
</section>

<aside class="provides">
  <h2 class="section-heading">Dr. Haldane Provides:</h2>
  <p>General dentistry – oral hygiene, cavity detection and repair, crowns.</p>
  <p>Cosmetic/restorative dentistry – broken or misshapen teeth, crooked smiles, unsightly gaps.</p>
  <p>Non-metal fillings – nontoxic, durable tooth-colored resin fillings that are proven to provide better results.</p>
  <p>Tooth shaping – contouring, shortening or otherwise reshaping teeth for improved esthetics.</p>
  <p>Complete smile make-over's – resin veneers that reshape the whole mouth while preserving natural teeth.</p>
  <p>Teeth whitening – at-home bleaching options to make teeth appear years younger.</p>
  <p>Laser Dentistry, Sleep Dentistry, and Implant Dentistry with the Finest and Latest Equipment and Materials.</p>
  <p>Dental Implants to replace missing teeth. Sedation Dentistry so you can be relaxed.</p>
  <div class="side-links">
    <a href="#">Office News and Blog Entries</a>
    <a href="#">What's in Play</a>
  </div>
</aside>

<main class="commitment">
  <h2 class="section-heading">Dr. Haldane' Commitment</h2>
  <p>After 20 years of teaching dentists how to refine their technique and many years of writing textbooks, I currently devote my time to my office and the hands-on practice of dentistry. I'd like to welcome you personally to my dental practice, and I invite you to meet my highly experienced team of professionals.</p>
  <p>Dr. Haldane and his Associated have offered complete dental care of the highest quality since 1978. We provide Preventive Services, Tooth Whitening and Cosmetic Dentistry for a beautiful smile, Endodontics (root canal treatment) to treat painful teeth, Sedation Dentistry so you can relax, and Dental Implants to restore what is missing. We offer total care.</p>
  <p>Our approach to your health is simple: We use our education, experience and dedication to provide every patient with superior dental care.</p>
  <p>This passion for excellence is not just a goal, but a standard every member of our team holds.</p>
  <p>We also pride ourselves with our state of the art procedures, training and technology. This includes creating a beautiful smile using techniques that preserve as much of the original tooth as possible.</p>
  <p>Our abilities are renowned throughout the dental profession and I hope if you have any questions you will contact us by an e-mail note, by phone or just by dropping by.</p>
  <p>Thank you.</p>
  <p>Sincerely,</p>
  <p class="signoff">Mara Haldane, DDS</p>
  <p class="offer">We offer an Initial Patient Examination, X-rays and Cleaning for $79.00.</p>
  <p class="fine">*New patients only. Offer not valid with insurance. May not be combined with other offers.</p>
  <p class="fine">Please contact us at (555) 014-2290.</p>
  <p class="fine">To contact us outside office hours for an emergency, please call (555) 014-2290.</p>
</main>

</body>
</html>
```